International Book about Player ethics in stadiums - This book will be presented to players in all

This book will be distributed to players to learn about the mathematical ethics, and the spirit of sport required for the ideal player
It also aims to teach the public the morals of encouragement and some instructions about keeping the playgrounds beautiful
Size : w 15 x 21 H
Title of the book
نجوم على ضفاف الغروب
Author
تاليف / الدكتور ناصر بن عيسى المرزوقي
1440-2018

Target Market(s)

This book will be presented to players in all activities

Colors

Designer to choose colors to be used in the design.

Requirements
Must have
• Selected colors must be related to play, players, activity and vitality.
• To be the attractive design makes the book lovable
• Final design of the file in the front and back should be on files illustrator and Photoshop and accept the opening on the lower versions
•  
Nice to have
• Example:
• Option 1
• stadium image
• The image must be for a mathematical expression
• For example: a player extends his hand to the opponent to help him from the ground or
• Two players from the two teams are hugging - shaking hands
• Option 2
• The picture can be a sports track
• On both sides of the track are the names of sports ethics - fair play - sportsmanship - compassion - clean encouragement - discipline - respect - apology ... etc
Should not have
• Direct images of famous players or people
• In the case of images should be indirect - or possible to be drawings
• Direct photos of famous people or players are not required

```html
<!DOCTYPE html>
<html lang="ar">
<head>
<meta charset="utf-8">
<title>نجوم على ضفاف الغروب — غلاف الكتاب</title>
<link rel="stylesheet" href="https://fonts.googleapis.com/css2?family=Cairo:wght@700;900&family=Noto+Sans+Arabic:wght@700&family=Cabin:wght@600&display=swap">
<style>
  :root {
    --page-bg: #d6eaf6;
    --sky-top: #5778b4;
    --sky-mid: #7f99c4;
    --sky-low: #a9bbd6;
    --cloud: #eef2f7;
    --stands: #3b414d;
    --stands-light: #6d7482;
    --pitch: #3f8d3b;
    --track: #d8553a;
    --track-deep: #b9412c;
    --title-ink: #5a0f1c;
    --white: #ffffff;
  }
  * { box-sizing: border-box; margin: 0; padding: 0; }
  html, body {
    width: 1200px;
    height: 1200px;
    overflow: hidden;
  }
  body {
    background: radial-gradient(circle at 50% 45%, #e6f3fb 0%, var(--page-bg) 70%);
    position: relative;
  }
  .book-cover {
    position: absolute;
    left: 280px;
    top: 120px;
    width: 640px;
    height: 960px;
    overflow: hidden;
    box-shadow: 0 10px 30px rgba(40, 70, 100, 0.25);
  }
  .cover-art {
    position: absolute;
    inset: 0;
    background: linear-gradient(to bottom,
      var(--sky-top) 0%,
      var(--sky-mid) 38%,
      var(--sky-low) 55%,
      var(--cloud) 63%,
      #c7d0dc 68%,
      var(--stands-light) 72%,
      var(--stands) 78%,
      #4a5160 83%,
      var(--pitch) 85%,
      var(--pitch) 87%,
      var(--track) 89%,
      var(--track-deep) 100%);
  }
  .author-line {
    position: absolute;
    top: 40px;
    left: 0;
    right: 0;
    text-align: center;
    direction: rtl;
    font-family: "Noto Sans Arabic", sans-serif;
    font-weight: 700;
    font-size: 23px;
    color: var(--white);
  }
  .book-title {
    position: absolute;
    top: 250px;
    left: 0;
    right: 0;
    text-align: center;
    direction: rtl;
    font-family: "Cairo", sans-serif;
    font-weight: 900;
    font-size: 84px;
    line-height: 124px;
    color: var(--title-ink);
    text-shadow:
      3px 0 0 var(--white), -3px 0 0 var(--white),
      0 3px 0 var(--white), 0 -3px 0 var(--white),
      2px 2px 0 var(--white), -2px -2px 0 var(--white),
      2px -2px 0 var(--white), -2px 2px 0 var(--white),
      4px 5px 6px rgba(0, 0, 0, 0.35);
  }
  .book-title span { display: block; }
  .ethics-list {
    position: absolute;
    bottom: 30px;
    left: 0;
    right: 0;
    display: flex;
    justify-content: space-around;
    padding: 0 30px;
    list-style: none;
    font-family: "Cabin", sans-serif;
    font-weight: 600;
    font-size: 23px;
    color: var(--white);
    text-shadow: 0 1px 3px rgba(0, 0, 0, 0.35);
  }
</style>
</head>
<body>
  <main class="book-cover">
    <div class="cover-art" role="img" aria-label="صورة ملعب رياضي بسماء زرقاء وغيوم وأضواء كاشفة ومدرجات ومضمار جري أحمر"></div>
    <p class="author-line">المؤلف/الدكتور ناصر بن عيسى المرزوقي</p>
    <h1 class="book-title">
      <span>نجوم على ضفاف</span>
      <span>الغروب</span>
    </h1>
    <ul class="ethics-list">
      <li>Respect</li>
      <li>Fair Play</li>
      <li>Apology</li>
      <li>Discipline</li>
    </ul>
  </main>
</body>
</html>
```